tinyTally Resource Book - 10 maths tasks to do outside

I need a 22 (11 pages back to back) page A6 sized book produced to standard for submission to professional printer. Needs to be as .pdf file showing guide lines and allowances for colour bleed. I have text already written and submitted as attachment in a Word file with margins set to A6 size. The theme of the materials is "Nature Play" so using lots of pictures from nature (Australia preferably) and showing lots of patterns in nature (rocks, leaves, flower petals etc). Some of the tasks refer to specific activities, such as "shadows" and "floating" so would be great to illustrate appropriately. The big emphasis is on learning outside the classroom, getting kids to engage actively with nature. I would like to see the pages as full colour - so not white background. The book itself will be spiral bound along the top edge so a margin of at least 1cm will be required at the top of each page (or the bottom of even numbered pages). Book will be printed on plastic laminated matte paper for outdoor use. Font size needs to be big enough to read. Fonts sizes, alignments and page numbers are all different at the moment and need to be standardised. One photo is included in a page as a sample if you can use it, otherwise disregard. Logo for Wattlebrook Numeracy Guild is also included to have as part of the acknowledgements at the back of the book.

Target Market(s)

Book is for early childhood and preschool teachers.

Industry/Entity Type

Education

Font styles to use
Sans Serif

Requirements
Must have
• Colour and appeal.
Nice to have
• Use of natural colours instead of bright catchy colours but that is your call.
Should not have
• American spelling

```html
<!DOCTYPE html>
<html lang="en-AU">
<head>
<meta charset="utf-8">
<title>tinyTally – Task 12: Insert your own idea</title>
<link rel="stylesheet" href="https://fonts.googleapis.com/css2?family=Jost:ital,wght@0,400;0,700;0,800;1,700&display=swap">
<style>
  :root {
    --paper: #ffffff;
    --trim-line: #555555;
    --page-peach: #f6b98c;
    --page-coral: #ec9d84;
    --page-glow: #fff4dc;
    --heading-blue: #2c3990;
    --prompt-blue: #2e3a92;
    --body-ink: #262626;
    --bullet-red: #d9282f;
    --figure-tone: #f7e27a;
  }
  * { margin: 0; padding: 0; box-sizing: border-box; }
  html, body {
    width: 892px; height: 1200px; overflow: hidden;
    background: var(--paper);
  }
  .sheet {
    position: relative; width: 892px; height: 1200px;
    font-family: "Jost", "Futura", sans-serif;
  }
  .crop-marks { position: absolute; inset: 0; }
  .page {
    position: absolute; left: 53px; top: 53px; width: 787px; height: 1095px;
    background:
      radial-gradient(circle at 62% 33%, var(--page-glow) 0%, rgba(255,240,210,0.85) 18%, rgba(250,205,160,0.5) 42%, rgba(246,185,140,0) 68%),
      radial-gradient(circle at 50% 40%, #f9c89a 0%, var(--page-peach) 60%, var(--page-coral) 100%);
    overflow: hidden;
  }
  .page__halo {
    position: absolute; left: 255px; top: 85px; width: 390px; height: 390px;
    border-radius: 50%; background: rgba(255,255,255,0.18);
  }
  .page__swirl {
    position: absolute; left: -120px; top: 280px; width: 1000px; height: 520px;
    border-radius: 50%; border: 2px solid rgba(255,255,255,0.35);
  }
  .task-title {
    position: absolute; left: 0; right: 0; top: 52px;
    text-align: center; color: var(--heading-blue);
    font-weight: 700; font-size: 47px; line-height: 62px;
    text-shadow: 2px 2px 0 #fff, -1px -1px 0 #fff, 1px -1px 0 #fff, -1px 1px 0 #fff;
  }
  .outcome {
    position: absolute; left: 0; right: 0; top: 190px;
    text-align: center; color: var(--heading-blue);
    font-weight: 700; font-size: 30px; line-height: 42px;
    text-shadow: 1px 1px 0 #fff;
  }
  .prompt {
    position: absolute; left: 71px;
    color: var(--prompt-blue); font-weight: 700; font-style: italic;
    font-size: 25px; line-height: 36.5px;
  }
  .statement {
    position: absolute; left: 143px;
    color: var(--body-ink); font-weight: 400; font-size: 32px; line-height: 46px;
  }
  .opportunities { position: absolute; left: 131px; top: 695px; list-style: none; }
  .opportunities li {
    position: relative; padding-left: 34px;
    color: var(--body-ink); font-size: 31px; line-height: 42px; margin-bottom: 0;
  }
  .opportunities li::before {
    content: ""; position: absolute; left: 4px; top: 12px; width: 17px; height: 17px;
    background: var(--bullet-red); transform: rotate(45deg);
  }
  .idea-figure {
    position: absolute; left: 619px; top: 667px; width: 140px; height: 215px;
    border-radius: 70px 70px 20px 20px;
    background: radial-gradient(circle at 60% 25%, #fff6b0 0%, var(--figure-tone) 35%, rgba(247,226,122,0.25) 100%);
  }
</style>
</head>
<body>
<div class="sheet">
  <svg class="crop-marks" width="892" height="1200" viewBox="0 0 892 1200" aria-hidden="true">
    <g stroke="var(--trim-line)" stroke-width="1" fill="none">
      <path d="M53 0V74M74 36V76M0 53H74M36 74H76"/>
      <path d="M839 0V74M818 36V76M892 53H818M856 74H816"/>
      <path d="M53 1200V1126M74 1164V1124M0 1147H74M36 1126H76"/>
      <path d="M839 1200V1126M818 1164V1124M892 1147H818M856 1126H816"/>
    </g>
  </svg>

  <section class="page">
    <div class="page__halo"></div>
    <div class="page__swirl"></div>

    <h1 class="task-title">12. Insert you own idea<br>here</h1>
    <h2 class="outcome">EYLF – Outcome 5: Children are effective<br>communicators</h2>

    <p class="prompt" style="top:290px">Children develop dispositions for learning such<br>as curiosity, cooperation, confidence, creativity,<br>commitment, enthusiasm, persistence, imagina-<br>tion and reflexivity when they...</p>
    <p class="statement" style="top:437px">are curious and enthusiastic<br>participants in their learning</p>

    <p class="prompt" style="top:526px">Educators promote this learning when they...</p>
    <p class="statement" style="top:563px">recognise and value children’s<br>involvement in learning</p>

    <p class="prompt" style="top:652px">This task provides an opportunity to:</p>
    <ul class="opportunities">
      <li>explore learning as<br>their own responsibility</li>
      <li>use creativity and imagination<br>to explore their world</li>
      <li>describe their wonderings<br>about the world using their own<br>language</li>
    </ul>

    <div class="idea-figure" role="img" aria-label="Cartoon illustration of a teacher pointing up at a glowing light bulb idea"></div>
  </section>
</div>
</body>
</html>
```